Brightwell Aero Services Logo

I need a website and logo for the parent company Brightwell Aero Services, which encompasses general aviation aircraft repair, small aircrat rental and flight school. The company is based in Lawrenceville, Georgia at the Tolleson county airport. A saying that can be incorporated somehere could be, "Quality flying is safe flying", "Safety in mind is no accident" ,. I need a website and logo.

The company started as a repair shop performing repairs and inspections on Harlan, Vantor, Delkin and Ralstead general aviation aircraft, all models of single engine piston, multi engine piston, and single engine turboprop with an emphasis on Harlan Solvane and AeroTurn turbo prop aircraft. We have se=ince entered the aircraft rental and flight instruction market using the Delkin 240 ang Harlan Ranger aircraft.

Number of Pages; I don't know. Maybe 5 ? A home page for Brightwell Aero Services, page for maintenance and repairs and a couple for the rental and school. The maintenance shop is busy, always has been. I need to get the rental and school advertised and busy.

I have a logo for the maintenance shop shirts, not for the school. I do not have the file. I paid a business locally to do that and print on the shirts. They have the file.

Target Market(s)

In our flight school rental fleet department, we are looking for persons wishing to obtain their private pilot license and continuing on into their commercial and instrument ratings. In the aircraft maintenance department, we are looking for new customers who want a better and more quality relationship with their aircraft maintenance provider who will give more detail and quality in the repairs with an emphasis on safety and fewer problems between scheduled maintenance cycles on their aircraft. Brightwell's owner, Dale Hutchins, has been performing aircraft maintenance in the Atlanta area for 27 years. He has built a steady customer base through those years.

```html
<!DOCTYPE html>
<html lang="en">
<head>
<meta charset="utf-8">
<title>Brightwell Aero Services</title>
<link rel="stylesheet" href="https://fonts.googleapis.com/css2?family=Rubik:wght@500;700&family=Barlow:wght@300;400&family=Barlow+Semi+Condensed:wght@500;600&family=Oswald:wght@300;400&family=Montserrat:wght@700&family=Great+Vibes&display=swap">
<style>
:root{
  --navy:#0c2430;
  --navy-deep:#081c26;
  --red:#e03a35;
  --text:#5e6a72;
  --white:#ffffff;
}
*{margin:0;padding:0;box-sizing:border-box}
html,body{width:1200px;height:2594px;overflow:hidden;background:var(--white)}
body{position:relative;font-family:'Barlow',sans-serif;color:var(--navy)}
.abs{position:absolute}
.brand{left:90px;top:30px;display:flex;align-items:center;gap:10px;font-family:'Rubik',sans-serif;font-weight:700;font-size:19px;line-height:1.1;color:var(--navy)}
.brand-dot{width:44px;height:44px;border-radius:50%;background:var(--navy)}
.nav{left:430px;top:47px;display:flex;gap:30px;font-family:'Oswald',sans-serif;font-weight:400;font-size:14px;color:var(--navy)}
.nav .active{color:var(--red)}
.btn{background:var(--red);color:var(--white);font-family:'Barlow Semi Condensed',sans-serif;font-weight:600;border-radius:30px;display:flex;align-items:center;justify-content:center}
.signup{left:945px;top:38px;width:148px;height:39px;font-size:14px}
.hero{left:0;top:117px;width:1200px;height:436px;background:linear-gradient(100deg,#8a98a3 0%,#75858f 55%,#5d6c76 100%)}
.hero-title{left:105px;top:210px;font-family:'Rubik',sans-serif;font-weight:700;font-size:70px;line-height:74px;letter-spacing:-1px}
.hero-title .dark{color:var(--navy)}
.hero-title .light{color:var(--white)}
.slide-card{left:104px;top:449px;width:645px;height:169px;background:var(--white);box-shadow:0 12px 30px rgba(0,0,0,.08);display:flex}
.slide-photo{width:249px;height:169px;background:radial-gradient(circle at 45% 45%,#f3a52a 0 18%,#1c2530 30%,#3b4450 100%)}
.slide-text{padding:33px 0 0 34px}
.slide-text p{font-family:'Oswald',sans-serif;font-weight:400;font-size:25px;line-height:33px;color:var(--navy)}
.slide-text a{display:block;margin-top:14px;color:var(--red);font-family:'Barlow Semi Condensed',sans-serif;font-weight:500;font-size:13px;text-decoration:none}
.prev,.next{top:553px;width:171px;height:65px;color:var(--white);font-family:'Barlow Semi Condensed',sans-serif;font-weight:600;font-size:13px;display:flex;align-items:center;justify-content:center}
.prev{left:749px;background:var(--navy)}
.next{left:919px;background:var(--red)}
.h2{font-family:'Rubik',sans-serif;font-weight:700;font-size:38px;line-height:43px;color:var(--navy)}
.about-title{left:104px;top:718px}
.about-copy{left:104px;top:828px;width:305px;font-size:13.5px;line-height:24px;color:var(--text)}
.about-copy p+p{margin-top:19px}
.about-btn{left:104px;top:1024px;width:177px;height:54px;font-size:13px}
.about-photo{left:447px;top:718px;width:306px;height:360px;background:linear-gradient(110deg,#f1f2f3 0 35%,#5b6670 55%,#38414a 100%)}
.quote{left:792px;top:718px;width:305px;height:360px;background:var(--navy);padding:50px 40px 0 54px;color:var(--white)}
.quote .mark{font-family:'Montserrat',sans-serif;color:var(--red);font-size:30px;line-height:30px}
.quote p{margin-top:10px;font-family:'Montserrat',sans-serif;font-weight:700;font-size:14px;line-height:25px}
.quote .sign{margin-top:22px;font-family:'Great Vibes',cursive;font-size:33px}
.service{width:230px}
.service svg{width:58px;height:58px;stroke:var(--red);fill:none;stroke-width:2}
.service h3{margin-top:16px;font-family:'Barlow Semi Condensed',sans-serif;font-weight:600;font-size:19px;color:var(--navy)}
.service p{margin-top:14px;font-size:13.5px;line-height:24px;color:var(--text)}
.story-photo{left:104px;top:1733px;width:607px;height:342px;background:linear-gradient(180deg,#3e5a5c 0%,#c7c8c4 45%,#bdbab3 100%)}
.story-title{left:765px;top:1726px;font-family:'Rubik',sans-serif;font-weight:500;font-size:32px;line-height:37px;color:var(--navy)}
.story-copy{left:765px;top:1806px;width:335px;font-family:'Oswald',sans-serif;font-weight:300;font-size:14px;line-height:25px;color:var(--text)}
.checks{left:765px;top:2004px;display:grid;grid-template-columns:170px 170px;row-gap:22px;font-family:'Oswald',sans-serif;font-size:15px;color:var(--navy)}
.checks span{display:flex;align-items:center;gap:12px}
.checks svg{width:16px;height:16px}
.footer{left:0;top:2211px;width:1200px;height:274px;background:var(--navy)}
.footer-brand{left:104px;top:2318px;display:flex;align-items:center;gap:12px;font-family:'Rubik',sans-serif;font-weight:700;font-size:22px;line-height:1.15;color:var(--white)}
.footer-brand .brand-dot{background:var(--white);width:50px;height:50px}
.contact{display:flex;gap:26px;color:var(--white)}
.contact svg{width:50px;height:72px;stroke:var(--red);fill:none;stroke-width:2}
.contact h4{font-family:'Rubik',sans-serif;font-weight:500;font-size:20px}
.contact p{margin-top:12px;font-family:'Barlow Semi Condensed',sans-serif;font-weight:500;font-size:12.5px;line-height:21px;color:#c8d0d5}
.bottom{left:0;top:2485px;width:1200px;height:109px;background:var(--navy-deep);display:flex;align-items:center;justify-content:center;font-family:'Oswald',sans-serif;font-weight:300;font-size:13px;color:#b7c0c6}
.bottom b{font-weight:400;color:var(--white)}
</style>
</head>
<body>

<header>
  <div class="abs brand"><span class="brand-dot"></span><span>Brightwell<br>Aero Services</span></div>
  <nav class="abs nav"><span class="active">Home</span><span>About Us</span><span>Maintenance &amp; Repair</span><span>Aircraft Rental</span><span>Flight Classes</span></nav>
  <div class="abs btn signup">Signup for a class</div>
</header>

<section>
  <div class="abs hero" role="img" aria-label="Mechanic working on an aircraft engine in a hangar"></div>
  <h1 class="abs hero-title"><span class="dark">We look</span><br><span class="light">after every detail</span></h1>
  <div class="abs slide-card">
    <div class="slide-photo" role="img" aria-label="Close-up of a jet engine fan with yellow spinner"></div>
    <div class="slide-text">
      <p>Quality flying is safe flying,<br>Safety in mind is no accident.</p>
      <a>Learn more &nbsp;›</a>
    </div>
  </div>
  <div class="abs prev">Prev</div>
  <div class="abs next">Next</div>
</section>

<section>
  <h2 class="abs h2 about-title">We stand for<br>excellence</h2>
  <div class="abs about-copy">
    <p>At this academy, the instructors are 100% committed to providing the highest quality flight training. We guarantee a supportive and friendly environment with a motivating professional team.</p>
    <p>The staff members are supported by a diverse fleet of impeccably maintained aircraft.</p>
  </div>
  <div class="abs btn about-btn">Read more about us</div>
  <div class="abs about-photo" role="img" aria-label="Technician servicing the propeller area of a small aircraft"></div>
  <div class="abs quote">
    <div class="mark">“</div>
    <p>Hello and welcome to Brightwell Aero Services. We Offer general aviation aircraft repair, alteration, small aircrat rental and flight school.</p>
    <div class="sign">Owen Pratt</div>
  </div>
</section>

<section>
  <div class="abs service" style="left:104px;top:1183px">
    <svg viewBox="0 0 58 58"><circle cx="29" cy="29" r="15"/><circle cx="29" cy="29" r="22" stroke-dasharray="8 5"/><path d="M22 29h14M29 22v14"/></svg>
    <h3>Basic maintenance</h3>
    <p>Management solutions. Full management of maintenance, leasing and exchange.</p>
  </div>
  <div class="abs service" style="left:362px;top:1183px">
    <svg viewBox="0 0 58 58"><circle cx="29" cy="29" r="25"/><circle cx="29" cy="29" r="18"/><circle cx="29" cy="29" r="4"/><path d="M29 11v14M29 33v14M11 29h14M33 29h14M17 17l9 9M32 32l9 9M41 17l-9 9M26 32l-9 9"/></svg>
    <h3>Engine, APU &amp; LG</h3>
    <p>Lean based process towards more effective TAT for AX320 family and C737 CL/NG.</p>
  </div>
  <div class="abs service" style="left:620px;top:1183px">
    <svg viewBox="0 0 58 58"><path d="M4 22l30 20-6 10L4 36z"/><path d="M34 8h18v40H34M40 4l10 10-14 14-6 2 2-6z"/><path d="M10 30l4 3M16 34l4 3"/></svg>
    <h3>Engineering &amp; design</h3>
    <p>Additional engineering course for aircraft designers with airworthiness management.</p>
  </div>
  <div class="abs service" style="left:878px;top:1183px">
    <svg viewBox="0 0 58 58"><circle cx="29" cy="24" r="20"/><path d="M29 44l-6 10M29 44l6 10M29 10v28M15 24h28M22 32h14"/></svg>
    <h3>Line maintenance</h3>
    <p>Available are lines &amp; station network in Europe, Africa, Russia &amp; CIS, Asia.</p>
  </div>
  <div class="abs service" style="left:104px;top:1416px">
    <svg viewBox="0 0 58 58"><path d="M6 16l22-10 24 10v26L28 54 6 42z"/><path d="M6 16l22 12 24-12M28 28v26M14 12l24 12"/><path d="M36 42h12M36 46h12"/></svg>
    <h3>Parts &amp; materials</h3>
    <p>Standing for excellence, we take a great care of the equipment and parts.</p>
  </div>
  <div class="abs service" style="left:362px;top:1416px">
    <svg viewBox="0 0 58 58"><rect x="9" y="8" width="40" height="48" rx="3"/><rect x="21" y="4" width="16" height="8"/><path d="M15 22h6v6h-6zM15 34h6v6h-6zM26 24h16M26 36h16M26 46h16M15 46h6"/></svg>
    <h3>Asset management</h3>
    <p>Technical asset management for lessors. Corvane 737 CL/NG, Aerolux 320 family. Upcoming Corvane 757.</p>
  </div>
  <div class="abs service" style="left:620px;top:1416px">
    <svg viewBox="0 0 58 58"><rect x="4" y="6" width="50" height="36"/><path d="M29 42v8M22 54h14M12 36V28M20 36V24M28 36V30M36 36V20M44 36V26M10 24l10-8 8 6 16-12"/></svg>
    <h3>Technical training</h3>
    <p>You can sign up for a practical or an online training course ESAR part 147.</p>
  </div>
  <div class="abs service" style="left:878px;top:1416px">
    <svg viewBox="0 0 58 58"><path d="M6 6h14l10 12-4 4-10-10H6zM30 18c6 0 12 6 12 12v16H16V34"/><circle cx="36" cy="20" r="5"/><path d="M12 54h36"/></svg>
    <h3>Cleaning &amp; fueling</h3>
    <p>We supervise and provide fuel availability, duties, airport fees and taxes.</p>
  </div>
</section>

<section>
  <div class="abs story-photo" role="img" aria-label="Busy maintenance hangar with several small aircraft"></div>
  <h2 class="abs story-title">Aircraft repair, rental<br>and flight school</h2>
  <p class="abs story-copy">The company started as a repair shop performing repairs and inspections on Harlan, Vantor, Delkin and Ralstead general aviation aircraft, all models of single engine piston, multi engine piston, and single engine turboprop with an emphasis on Harlan Solvane and AeroTurn turbo prop aircraft. We have se=ince entered the aircraft rental and flight instruction market using the Delkin 240 ang Harlan Ranger aircraft.</p>
  <div class="abs checks">
    <span><svg viewBox="0 0 16 16"><circle cx="8" cy="8" r="8" fill="#e03a35"/><path d="M4.5 8.2l2.3 2.3 4.7-5" stroke="#fff" stroke-width="2" fill="none"/></svg>Aircraft Repair</span>
    <span><svg viewBox="0 0 16 16"><circle cx="8" cy="8" r="8" fill="#e03a35"/><path d="M4.5 8.2l2.3 2.3 4.7-5" stroke="#fff" stroke-width="2" fill="none"/></svg>Alteration Service</span>
    <span><svg viewBox="0 0 16 16"><circle cx="8" cy="8" r="8" fill="#e03a35"/><path d="M4.5 8.2l2.3 2.3 4.7-5" stroke="#fff" stroke-width="2" fill="none"/></svg>Refinishing</span>
    <span><svg viewBox="0 0 16 16"><circle cx="8" cy="8" r="8" fill="#e03a35"/><path d="M4.5 8.2l2.3 2.3 4.7-5" stroke="#fff" stroke-width="2" fill="none"/></svg>Flight School</span>
  </div>
</section>

<footer>
  <div class="abs footer"></div>
  <div class="abs footer-brand"><span class="brand-dot"></span><span>Brightwell<br>Aero Services</span></div>
  <div class="abs contact" style="left:448px;top:2306px">
    <svg viewBox="0 0 50 72"><rect x="6" y="2" width="38" height="68" rx="4"/><path d="M6 12h38M6 58h38M20 34l6-6M22 40l8-8"/></svg>
    <div><h4>1.800.555.01.42</h4><p>Working hours:<br>Monday — Friday: 8.00am - 9.00pm</p></div>
  </div>
  <div class="abs contact" style="left:796px;top:2306px">
    <svg viewBox="0 0 50 72"><path d="M25 66C10 44 2 34 2 24a23 23 0 0146 0c0 10-8 20-23 42z"/><circle cx="25" cy="24" r="9"/><path d="M6 71h38"/></svg>
    <div><h4>Tolleson Airport</h4><p>418 N Carrow ave<br>Crestfield, Harrow County</p></div>
  </div>
  <div class="abs bottom"><span>Copyright 2023 <b>Brightwell Aero Services</b>, All rights reserved.</span></div>
</footer>

</body>
</html>
```